Software Development Consulting Company Needs Business Card Design

We need a new business card design for our consultants at Kestrel Works (kestrelworks.example). We are a small firm that provides high-end software development and methodology consulting to medium to large enterprise IT organizations.

Our logo uses Futura for the font and we would like to stick with navy blue and canary yellow for the logo colors. Attached are normal and reversed versions of our logos in illustrator format.
Updates

Hi Everyone, Thank yo very much for your amazing design ideas. I have created a poll for this project and our employees will be voting on the design they wish to use. We will be making a decision this Wednesday (October 22nd). Thanks again, Dale Hartwick

Industry/Entity Type

Business

```html
<!DOCTYPE html>
<html lang="en">
<head>
<meta charset="utf-8">
<title>Kestrel Works — Business Card</title>
<link rel="stylesheet" href="https://fonts.googleapis.com/css2?family=Jost:wght@500&family=Open+Sans:wght@400;700&display=swap">
<style>
  :root {
    --navy: #1f4a73;
    --slate: #8e9db4;
    --canary: #ffef00;
    --paper: #ffffff;
    --ink: #3a3a3a;
    --backdrop: #e9e9ee;
  }
  * { box-sizing: border-box; margin: 0; padding: 0; }
  html, body {
    width: 1200px; height: 980px; overflow: hidden;
    background: var(--backdrop);
    font-family: "Open Sans", Arial, sans-serif;
  }
  .stage {
    position: relative; width: 1200px; height: 980px;
  }
  .card {
    position: absolute; left: 250px; width: 700px; height: 400px;
    border-radius: 28px; overflow: hidden;
    box-shadow: 0 6px 18px rgba(0,0,0,.12);
  }
  .card--front { top: 70px; background: var(--paper); }
  .card--back { top: 510px; background: var(--canary); }

  .wordmark {
    display: flex; align-items: center; gap: 14px;
    font-family: "Jost", "Futura", sans-serif; font-weight: 500;
    color: var(--navy); letter-spacing: 4px; text-transform: uppercase;
  }
  .wordmark__dot {
    border: 5px solid var(--navy); border-radius: 50%;
  }
  .card--front .wordmark {
    position: absolute; left: 150px; top: 62px; font-size: 50px;
  }
  .card--front .wordmark__dot { width: 46px; height: 46px; }

  .card__bands { position: absolute; left: 0; top: 0; }

  .identity {
    position: absolute; left: 150px; top: 170px; width: 210px; text-align: right;
    color: var(--ink);
  }
  .identity__name { font-size: 22px; font-weight: 700; color: var(--navy); }
  .identity__title { font-size: 15px; margin-top: 2px; }
  .identity__place { font-size: 14px; margin-top: 10px; display: flex; justify-content: flex-end; align-items: center; gap: 6px; }

  .divider {
    position: absolute; left: 378px; top: 172px; width: 1px; height: 92px; background: #bfc4cc;
  }

  .contact {
    position: absolute; left: 396px; top: 190px; color: var(--ink); font-size: 16px;
  }
  .contact__row { display: flex; align-items: center; gap: 8px; margin-bottom: 14px; }

  .card__url {
    position: absolute; right: 40px; bottom: 22px;
    color: var(--paper); font-size: 20px; letter-spacing: 4px;
  }

  .card--back .wordmark {
    position: absolute; left: 0; right: 0; top: 150px; justify-content: center;
    font-size: 60px;
  }
  .card--back .wordmark__dot { width: 54px; height: 54px; }
  .card--back .card__url {
    left: 60px; right: auto; bottom: 50px; color: var(--navy); font-weight: 700; font-size: 20px;
  }
</style>
</head>
<body>
<main class="stage">
  <section class="card card--front" aria-label="Business card front">
    <svg class="card__bands" width="700" height="400" viewBox="0 0 700 400" aria-hidden="true">
      <polygon points="0,262 200,262 240,302 0,302" fill="var(--slate)"/>
      <polygon points="0,302 240,302 268,330 700,330 700,400 0,400" fill="var(--navy)"/>
    </svg>

    <div class="wordmark"><span class="wordmark__dot"></span>Kestrel Works</div>

    <div class="identity">
      <p class="identity__name">Your Name</p>
      <p class="identity__title">Title</p>
      <p class="identity__place">
        <svg width="12" height="16" viewBox="0 0 12 16" aria-hidden="true"><path d="M6 0a6 6 0 0 0-6 6c0 4.5 6 10 6 10s6-5.5 6-10a6 6 0 0 0-6-6zm0 8.5A2.5 2.5 0 1 1 6 3.5a2.5 2.5 0 0 1 0 5z" fill="var(--navy)"/></svg>
        Lakeport, Millbrook, IL
      </p>
    </div>

    <div class="divider"></div>

    <div class="contact">
      <p class="contact__row">
        <svg width="18" height="18" viewBox="0 0 18 18" aria-hidden="true"><circle cx="9" cy="9" r="8" fill="none" stroke="var(--navy)" stroke-width="1.6"/><path d="M6 5l2 2-1 1.2c.6 1.2 1.5 2.1 2.8 2.8L11 10l2 2-1.2 1.2C9 13 5 9 4.8 6.2z" fill="var(--navy)"/></svg>
        012-345-6789
      </p>
      <p class="contact__row">
        <svg width="18" height="14" viewBox="0 0 18 14" aria-hidden="true"><rect x="1" y="1" width="16" height="12" rx="2" fill="none" stroke="var(--navy)" stroke-width="1.6"/><path d="M1.5 2l7.5 6 7.5-6" fill="none" stroke="var(--navy)" stroke-width="1.6"/></svg>
        info@kestrelworks.example
      </p>
    </div>

    <p class="card__url">www.kestrelworks.example</p>
  </section>

  <section class="card card--back" aria-label="Business card back">
    <div class="wordmark"><span class="wordmark__dot"></span>Kestrel Works</div>
    <p class="card__url">www.kestrelworks.example</p>
  </section>
</main>
</body>
</html>
```